Support People to improve their image and well-being by provided personalised advise

We need a design for business cards that could be used for production on plano press. We build a new business in our region for advising mostly women (also men though) on style embracing several aspects including fashion, style, self-confidence and ultimately your internal and external image. The business card should be "classy", "french-style". The business is located in the french -speaking part of Switzerland, close to France. The name of the company is Lomu Grace

Target Market(s)

Service fees won't be cheap (medium to premium) thus we target mid-class to upper-class women (1st target) and men (2nd target)

Industry/Entity Type

Life Coaching

Contact Information for Business Card

Conseil en Image

+41 76 418 63 07
tovasel@lomu-grace.example
linkedin.example/in/sel-moran-tova

Logo Text

Lomu Grace

Colors

Designer to choose colors to be used in the design.

```html
<!DOCTYPE html>
<html lang="fr">
<head>
<meta charset="utf-8">
<title>Lomu Grace – Cartes de visite</title>
<link rel="stylesheet" href="https://fonts.googleapis.com/css2?family=Jost:wght@400;500&family=Kalam:wght@700&display=swap">
<style>
  :root {
    --backdrop: #bdbdbd;
    --charcoal: #363a3d;
    --paper: #f2f2f1;
    --gold: #b99468;
    --gold-light: #d9bd96;
    --ink: #2f3336;
    --silver: #c9c9c9;
  }
  * { margin: 0; padding: 0; box-sizing: border-box; }
  html, body { width: 1200px; height: 576px; overflow: hidden; }
  body {
    background: var(--backdrop);
    position: relative;
    font-family: "Jost", "Helvetica Neue", Arial, sans-serif;
  }
  .card {
    position: absolute;
    width: 484px;
    height: 292px;
    border-radius: 16px;
    overflow: hidden;
  }
  .card--front { left: 82px; top: 139px; background: var(--charcoal); }
  .card--back { left: 602px; top: 138px; background: var(--paper); }

  .brand {
    position: absolute;
    display: flex;
    flex-direction: column;
    align-items: center;
    gap: 18px;
    transform: translateX(-50%);
  }
  .brand__dot {
    width: 40px; height: 40px; border-radius: 50%;
    background: linear-gradient(135deg, var(--gold-light), var(--gold));
  }
  .brand__name {
    font-weight: 400;
    font-size: 26px;
    letter-spacing: 5px;
    white-space: nowrap;
    text-transform: uppercase;
  }
  .card--front .brand { left: 242px; top: 110px; }
  .card--front .brand__name { color: var(--silver); }
  .card--back .brand { left: 360px; top: 58px; }
  .card--back .brand__name { color: var(--ink); font-size: 24px; }

  .person { position: absolute; left: 30px; top: 40px; }
  .person__name {
    font-family: "Kalam", "Comic Sans MS", cursive;
    font-weight: 700;
    font-size: 24px;
    color: var(--gold);
    line-height: 1.1;
  }
  .person__role { font-size: 12.5px; color: var(--ink); margin-top: 2px; }

  .contact { position: absolute; left: 30px; top: 208px; list-style: none; }
  .contact__item {
    display: flex; align-items: center; gap: 10px;
    font-size: 13px; color: var(--ink); height: 18px;
  }
  .contact__icon { width: 11px; height: 11px; fill: var(--ink); }

  .footer-band { position: absolute; left: 0; bottom: 0; width: 484px; height: 30px; }
</style>
</head>
<body>

<section class="card card--front" aria-label="Recto">
  <div class="brand">
    <span class="brand__dot"></span>
    <span class="brand__name">Lomu Grace</span>
  </div>
</section>

<section class="card card--back" aria-label="Verso">
  <div class="person">
    <p class="person__name">Sel Moran Tova</p>
    <p class="person__role">Conseil en Image</p>
  </div>

  <div class="brand">
    <span class="brand__dot"></span>
    <span class="brand__name">Lomu Grace</span>
  </div>

  <ul class="contact">
    <li class="contact__item">
      <svg class="contact__icon" viewBox="0 0 12 12"><path d="M1 4c0-2 2-3 5-3s5 1 5 3v1H8V4H4v1H1zM3 6h6l2 5H1z"/></svg>
      +41 76 418 63 07
    </li>
    <li class="contact__item">
      <svg class="contact__icon" viewBox="0 0 12 12"><path d="M0 2h12v8H0z M1 3l5 4 5-4" stroke="#f2f2f1" stroke-width="1"/></svg>
      tovasel@lomu-grace.example
    </li>
    <li class="contact__item">
      <svg class="contact__icon" viewBox="0 0 12 12"><circle cx="6" cy="6" r="5.5"/><path d="M0.5 6h11M6 0.5v11M6 0.5c-3 3-3 8 0 11M6 0.5c3 3 3 8 0 11" stroke="#f2f2f1" stroke-width="0.8" fill="none"/></svg>
      www.lomu-grace.example
    </li>
  </ul>

  <svg class="footer-band" viewBox="0 0 484 30" aria-hidden="true">
    <defs>
      <linearGradient id="gold-band" x1="0" x2="1">
        <stop offset="0" stop-color="#c7a276"/>
        <stop offset="1" stop-color="#ddc39e"/>
      </linearGradient>
    </defs>
    <rect x="0" y="20" width="260" height="10" fill="var(--charcoal)"/>
    <path d="M230 30 L252 2 Q254 0 258 0 H484 V30 Z" fill="url(#gold-band)"/>
  </svg>
</section>

</body>
</html>
```